Education Certificate

We need a modern yet professional Certificate for those who successfully pass / complete our online Training course.

There are various courses but ONE certificate design required.

the certificate needs to look extremely professional and of value.

```html
<!DOCTYPE html>
<html lang="en">
<head>
<meta charset="utf-8">
<title>Certificate of Completion</title>
<link rel="stylesheet" href="https://fonts.googleapis.com/css2?family=Arimo:ital,wght@0,400;0,700;1,700&family=Montserrat:wght@700&family=Open+Sans:wght@800&family=Playfair+Display:wght@900&display=swap">
<style>
  :root {
    --navy: #1e2f6b;
    --navy-deep: #1b2a62;
    --navy-soft: #2c3f80;
    --gold: #ffd200;
    --white: #ffffff;
    --ink: #1e2f6b;
    --sign-tone: #e6e9f2;
  }
  * { margin: 0; padding: 0; box-sizing: border-box; }
  html, body { width: 1200px; height: 848px; overflow: hidden; background: var(--white); }
  .certificate {
    position: relative;
    width: 1200px;
    height: 848px;
    background: var(--navy);
    padding: 11px;
    font-family: "Arimo", Arial, sans-serif;
    color: var(--ink);
  }
  .sheet {
    position: relative;
    width: 100%;
    height: 100%;
    background: var(--white);
    overflow: hidden;
  }
  .corner {
    position: absolute;
    width: 48px;
    height: 48px;
    border-radius: 50%;
    background: var(--navy);
  }
  .corner--tl { left: -24px; top: -24px; }
  .corner--tr { right: -24px; top: -24px; }
  .corner--bl { left: -24px; bottom: -24px; }
  .corner--br { right: -24px; bottom: -24px; }

  .ribbon {
    position: absolute;
    left: 932px;
    top: 0;
    width: 170px;
    height: 641px;
    background: var(--navy-deep);
    clip-path: polygon(0 0, 100% 0, 100% 100%, 50% 89.5%, 0 100%);
  }
  .seal {
    position: absolute;
    left: 887px;
    top: 200px;
    width: 262px;
    height: 262px;
    border-radius: 50%;
    background: radial-gradient(circle at 50% 45%, var(--navy-soft), var(--navy));
    box-shadow: 0 6px 14px rgba(0,0,0,0.25);
  }

  .brand {
    position: absolute;
    left: 75px;
    top: 96px;
    width: 190px;
    display: flex;
    align-items: flex-start;
    gap: 10px;
  }
  .brand__mark {
    flex: none;
    width: 16px;
    height: 16px;
    margin-top: 3px;
    background: var(--gold);
  }
  .brand__name {
    font-family: "Montserrat", Arial, sans-serif;
    font-weight: 700;
    font-size: 17px;
    line-height: 1.2;
    letter-spacing: 0.5px;
    text-transform: uppercase;
    color: var(--navy);
  }
  .brand__divider {
    position: absolute;
    left: 271px;
    top: 99px;
    width: 2px;
    height: 76px;
    background: var(--navy);
  }
  .title {
    position: absolute;
    left: 295px;
    top: 82px;
    font-family: "Playfair Display", Georgia, serif;
    font-weight: 900;
    color: var(--navy);
  }
  .title__main { display: block; font-size: 72px; line-height: 1; letter-spacing: -1px; }
  .title__sub { display: block; font-size: 27px; line-height: 1; margin-top: 4px; margin-left: 3px; }

  .recipient {
    position: absolute;
    left: 75px;
    top: 274px;
    font-family: "Open Sans", Arial, sans-serif;
    font-weight: 800;
    font-size: 68px;
    line-height: 1;
    letter-spacing: -0.5px;
    color: var(--gold);
  }
  .lead {
    position: absolute;
    left: 76px;
    top: 352px;
    font-size: 20px;
  }
  .course {
    position: absolute;
    left: 75px;
    top: 401px;
    width: 840px;
  }
  .course__name {
    font-size: 20.5px;
    font-weight: 700;
    letter-spacing: 0.2px;
    margin-bottom: 12px;
  }
  .course__text {
    font-size: 17px;
    line-height: 19px;
    width: 630px;
    margin-bottom: 19px;
  }
  .completed-on {
    position: absolute;
    left: 75px;
    top: 581px;
    font-size: 21px;
  }
  .signature {
    position: absolute;
    left: 75px;
    top: 650px;
    width: 195px;
  }
  .signature__mark {
    width: 160px;
    height: 58px;
    margin-left: 6px;
    border-radius: 4px;
    background: linear-gradient(90deg, var(--sign-tone), #f4f5f9);
  }
  .signature__line {
    height: 1px;
    background: var(--navy);
    margin-top: 10px;
  }
  .signature__role {
    text-align: center;
    margin-top: 6px;
    font-size: 16px;
    font-weight: 700;
    font-style: italic;
    padding-right: 24px;
  }
</style>
</head>
<body>
<main class="certificate">
  <div class="sheet">
    <span class="corner corner--tl"></span>
    <span class="corner corner--tr"></span>
    <span class="corner corner--bl"></span>
    <span class="corner corner--br"></span>

    <div class="ribbon"></div>
    <div class="seal" role="img" aria-label="Completion seal badge"></div>

    <div class="brand">
      <span class="brand__mark"></span>
      <span class="brand__name">Global Service Excellence Academy</span>
    </div>
    <span class="brand__divider"></span>

    <h1 class="title">
      <span class="title__main">Certificate</span>
      <span class="title__sub">of Completion</span>
    </h1>

    <p class="recipient">Amelia Hartwell</p>
    <p class="lead">has completed the following course:</p>

    <section class="course">
      <h2 class="course__name">DIGITAL SERVICE EXPERIENCE FRAMEWORK DSEF2024</h2>
      <p class="course__text">DSEF2024 reflects the increased international growth in scale, reach and scope of digital transformation and services delivered through Digital Channels.</p>
      <p class="course__text">The primary aim of the DSEF2024 Framework is to motivate organisations to focus their attention on the Digital Customer Experience through the delivery of service excellence techniques</p>
    </section>

    <p class="completed-on">on March 20, 2024</p>

    <div class="signature">
      <div class="signature__mark" role="img" aria-label="Handwritten signature of Daniel Moreno"></div>
      <div class="signature__line"></div>
      <p class="signature__role">CEO, GSEA</p>
    </div>
  </div>
</main>
</body>
</html>
```